PAX

We need to design a power point presentation that can englobe all our company products.

This presentation has to have all the required to be used as template for future presentations.

We focus on prodcut developing for supermarkets, ( we help them with their own brand products ex. Sunny Harvest, TK, etc.)
Also we are on the marine industry, we develop ships and oil rigs for the Oil and deep water market.

Target Market(s)

Oil Companies
Supermarket companies
Retail Companies

Industry/Entity Type

It Company

Requirements
Must have
• Our Logo and company colors
Nice to have
• Something describing globalization.
Should not have
• Orange color

```html
<!DOCTYPE html>
<html lang="en">
<head>
<meta charset="utf-8">
<title>PAX Presentation Template</title>
<link rel="stylesheet" href="https://fonts.googleapis.com/css2?family=Michroma&family=Arimo:wght@400&display=swap">
<style>
  :root {
    --title-blue: #1f3a8f;
    --heading-blue: #1a6bbf;
    --band-blue: #0a6cc0;
    --accent-green: #8dc63f;
    --page-bg: #efefef;
    --text-dark: #222222;
    --white: #ffffff;
    --frame-border: #d4d4d4;
  }
  * { margin: 0; padding: 0; box-sizing: border-box; }
  html, body { width: 1200px; height: 900px; overflow: hidden; background: var(--page-bg); }
  .slide {
    position: relative;
    width: 1200px;
    height: 900px;
    overflow: hidden;
    background: radial-gradient(ellipse at 55% 50%, #f6f6f6 0%, var(--page-bg) 60%, #e9e9e9 100%);
    font-family: "Arimo", Arial, sans-serif;
  }
  .title-bar {
    position: absolute;
    left: 0; top: 0;
    width: 1200px; height: 86px;
    background: var(--white);
    border-bottom: 2px solid var(--accent-green);
  }
  .project-title {
    position: absolute;
    left: 38px; top: 24px;
    font-family: "Michroma", "Arial Black", sans-serif;
    font-size: 37px;
    font-weight: 400;
    letter-spacing: 1px;
    color: var(--title-blue);
    -webkit-text-stroke: 1.2px var(--title-blue);
    line-height: 1;
  }
  .brand-tab {
    position: absolute;
    left: 1008px; top: 0;
    width: 148px; height: 207px;
    background: var(--white);
    border-radius: 0 0 40px 40px;
    box-shadow: 0 2px 8px rgba(0,0,0,0.18);
    display: flex;
    flex-direction: column;
    align-items: center;
    justify-content: center;
    gap: 14px;
  }
  .brand-dot {
    width: 56px; height: 56px;
    border-radius: 50%;
    background: var(--heading-blue);
  }
  .brand-name {
    font-family: "Michroma", sans-serif;
    font-size: 30px;
    color: var(--heading-blue);
    line-height: 1;
  }
  .content-block {
    position: absolute;
    left: 38px;
    width: 680px;
  }
  .content-block.first { top: 213px; }
  .content-block.second { top: 500px; }
  .content-heading {
    font-family: "Michroma", sans-serif;
    font-size: 29px;
    font-weight: 400;
    color: var(--heading-blue);
    -webkit-text-stroke: 0.9px var(--heading-blue);
    line-height: 1.2;
    margin-bottom: 12px;
  }
  .content-text {
    font-size: 21.5px;
    line-height: 36px;
    color: var(--text-dark);
  }
  .photo-frame {
    position: absolute;
    left: 746px;
    width: 300px;
    background: var(--white);
    border: 1px solid var(--frame-border);
    box-shadow: 0 1px 4px rgba(0,0,0,0.15);
    padding: 5px;
  }
  .photo-frame.first { top: 226px; height: 200px; }
  .photo-frame.second { top: 501px; height: 201px; }
  .photo {
    width: 100%; height: 100%;
  }
  .photo.offshore { background: linear-gradient(180deg, #a9c7e3 0%, #7fa6cc 40%, #2f5f95 60%, #1f4c80 100%); }
  .photo.cruise { background: linear-gradient(180deg, #3f8fd6 0%, #6fb0e4 35%, #1c5fa8 55%, #0f3f7d 100%); }
  .footer-band {
    position: absolute;
    left: 0; top: 849px;
    width: 1200px; height: 51px;
    background: var(--band-blue);
  }
</style>
</head>
<body>
<main class="slide">
  <header class="title-bar">
    <h1 class="project-title">PROJECT TITLE HERE</h1>
  </header>

  <div class="brand-tab">
    <span class="brand-dot"></span>
    <span class="brand-name">PAX</span>
  </div>

  <section class="content-block first">
    <h2 class="content-heading">Content Heading Here</h2>
    <p class="content-text">Sub content here Sub content here Sub content here Sub content here Sub content here Sub content here Sub content here Sub content here Sub content here Sub content here Sub content here Sub content here</p>
  </section>
  <figure class="photo-frame first">
    <div class="photo offshore" role="img" aria-label="Offshore supply vessel sailing beside an oil rig at sea"></div>
  </figure>

  <section class="content-block second">
    <h2 class="content-heading">Content Heading Here</h2>
    <p class="content-text">Sub content here Sub content here Sub content here Sub content here Sub content here Sub content here Sub content here Sub content here Sub content here Sub content here Sub content here Sub content here</p>
  </section>
  <figure class="photo-frame second">
    <div class="photo cruise" role="img" aria-label="White cruise ship sailing on open blue sea"></div>
  </figure>

  <footer class="footer-band"></footer>
</main>
</body>
</html>
```